Home page design for Drone video business (the Business focusses on home videos for realtors)

Dear reader,

*I NEED DESIGNS OF ALL THE PAGES*
We need a first design of a homepage and of 4 other pages of the website of a business that sells drone video services. All the pages will need to be in the similar design style.
The video's are targeted at consumers that want to sell there home and would like to have a cool drone video of photos of their home.

How does the website look:
- has a navbar on top
- A cool looking banner of an areal drone.
- A Big header: with company name: SkyLoftReels
- A smaller subheader: We film your home to increase your chances of sale
- Then a section with a Big header: How does it work
- In this section a place for a vimeo explainitory video
- Then a similar navbar styled bar with a phone number and a email address
- Then a section where the videos porfolio is displayed in a cool way
- Inside this sectiona header: Our work

- A section with header: Why us?
- 4 symbols here with a subheader and some lorum ipsum text underneath (see wireframe images)

- Under that a: Contact us
- where you can put in name, email, phone, message box and a send button

- At the bottom a footer with phone number and a fake address for now.

Be creative. Use creative but serious color.
Use a serious font. Make it a sharp design. Sharp lines. Not to dark design and not to light design.

The wireframes are the same kind of images.
PLEASE PUT IN DESIGNS OF ALL THE PAGES

Good luck

Target Market(s)

People that want to sell home and want to make a cool drone video or photos of their home.

Industry/Entity Type

Business

Contact Information for Business Card

Lucas Wenning
lucas@skyloftreels.example
+31647208351

Logo Text

SkyLoftReels

Number of Pages Required

1 page

Font styles to use
Sans Serif

Requirements
Must have
• All the sections as explained in the instructions.
• The nav bar should have an about us, services, portfolio and a contact us buttons.
• See instruction for details.
• Must include designs of the front page, contact us, our services, portfolio and contact us.
• If you do add some designs for the "about us", "services", "prices", "portfolio" and "contact us" pages, you make a way better chance of winning the competition.
Nice to have
• designs for the other pages as described at the Must haves. You make a better chance of winning if you include them. Look at the wireframes to see the mockups for those pages. think creative about what kind of sections and design should be included in those pages.
Should not have
• bad designs.

```html
<!DOCTYPE html>
<html lang="en">
<head>
<meta charset="utf-8">
<title>SkyLoftReels – Home</title>
<link href="https://fonts.googleapis.com/css2?family=Raleway:wght@400;500;600;700&family=Open+Sans:wght@400;600&display=swap" rel="stylesheet">
<style>
:root{
  --teal:#0e6b73;
  --teal-dark:#0a5960;
  --teal-light:#3fb3b8;
  --teal-icon:#1a858d;
  --teal-panel:rgba(14,107,115,.72);
  --ink:#2b2b2b;
  --body:#3a3a3a;
  --grey-bg:#efefef;
  --dark-circle:#454545;
  --white:#ffffff;
}
*{margin:0;padding:0;box-sizing:border-box}
html,body{width:1200px;height:2683px;overflow:hidden;background:#fff}
body{font-family:"Raleway",sans-serif;color:var(--ink)}
.page{position:relative;width:1200px;height:2683px;overflow:hidden}
.abs{position:absolute}

/* header */
.site-header{top:0;left:0;width:1200px;height:102px;background:#fff;border-bottom:3px solid var(--teal)}
.brand{left:98px;top:24px;display:flex;align-items:center;gap:14px}
.brand-mark{width:46px;height:46px;background:var(--teal)}
.brand-name{font-weight:700;font-size:24px;color:var(--teal)}
.top-contact{right:100px;top:14px;display:flex;gap:28px;font-family:"Open Sans",sans-serif;font-size:15px;color:#333}
.top-contact span{display:flex;align-items:center;gap:12px}
.ring{width:30px;height:30px;border:1.5px solid #555;border-radius:50%;display:flex;align-items:center;justify-content:center}
.main-nav{right:98px;top:64px;display:flex;gap:48px;font-size:13px;font-weight:500;color:#333}
.main-nav .active{color:var(--teal);font-weight:700}

/* hero */
.hero{top:102px;left:0;width:1200px;height:556px;background:linear-gradient(110deg,#6f8e5a 0%,#d9dde0 25%,#7b9fc8 55%,#1b2a1f 80%,#2c4a25 100%)}
.hero-title{right:100px;top:328px;font-size:27px;font-weight:700;color:var(--teal-light);text-align:right}
.hero-sub{right:100px;top:368px;font-size:13px;font-weight:500;color:#fff}

/* section headings */
.section-title{width:1200px;left:0;text-align:center;font-size:32px;font-weight:400;color:var(--ink)}
.section-title b{font-weight:700;color:var(--teal)}
.section-title.on-dark,.section-title.on-dark b{color:var(--white)}
.rule{left:573px;width:54px;height:3px;background:var(--ink)}
.rule.on-dark{background:var(--white)}

/* how it works */
.how{top:658px;left:0;width:1200px;height:481px;background:var(--grey-bg)}
.video-slot{left:402px;top:787px;width:412px;height:352px;background:linear-gradient(180deg,#2a2a2a,#111);border-radius:14px 14px 0 0}
.video-screen{left:436px;top:817px;width:342px;height:256px;background:linear-gradient(180deg,#8fb4da,#a9a48a 55%,#5e7d3c)}
.play{width:62px;height:62px;border-radius:50%;background:rgba(255,255,255,.75);display:flex;align-items:center;justify-content:center}

/* help bar */
.help-bar{top:1139px;left:0;width:1200px;height:79px;background:var(--teal);color:#fff}
.help-title{left:160px;top:18px;font-size:34px;font-weight:700}
.help-icon{top:0;width:55px;height:79px;background:var(--teal-icon);display:flex;align-items:center;justify-content:center}
.help-text{top:22px;font-size:26px;font-weight:500;white-space:nowrap}

/* work */
.work{top:1218px;left:0;width:1200px;height:334px;background:linear-gradient(180deg,#3a4033,#2b2e27 60%,#3e3a30)}
.thumb{top:1345px;width:293px;height:162px;border:4px solid #fff;background:linear-gradient(180deg,#6f9fd6,#9fb0b8 55%,#4f7a33);display:flex;align-items:center;justify-content:center}
.arrow{top:1409px;width:32px;height:32px;background:rgba(255,255,255,.22);border:1px solid rgba(255,255,255,.4);display:flex;align-items:center;justify-content:center}

/* why */
.why{top:1552px;left:0;width:1200px;height:431px;background:#fff}
.feature{width:316px;font-family:"Open Sans",sans-serif}
.feature h3{font-family:"Raleway",sans-serif;font-size:19px;font-weight:700;margin-bottom:4px}
.feature.left{text-align:right}
.feature.left h3{color:var(--teal)}
.feature.right h3{color:var(--ink)}
.feature p{font-size:12.5px;line-height:21px;color:var(--body)}
.feature a{font-size:12px;color:var(--teal);text-decoration:none;display:block;margin-top:2px}
.icon-circle{width:114px;height:114px;border-radius:50%;background:var(--dark-circle);border:4px solid #2d2d2d;display:flex;align-items:center;justify-content:center}
.icon-circle.on{background:var(--teal);border-color:var(--teal-dark)}

/* contact */
.contact{top:1983px;left:0;width:1200px;height:700px;background:linear-gradient(180deg,#243023,#3a4636 40%,#4c5445 70%,#2f3529)}
.contact-panel{left:209px;top:2135px;width:780px;height:431px;background:var(--teal-panel)}
.send-icon{left:571px;top:2108px;width:58px;height:58px;border-radius:50%;background:#fff;display:flex;align-items:center;justify-content:center}
.contact-info{left:0;width:1200px;text-align:center;color:#fff;font-family:"Open Sans",sans-serif;font-size:12.5px;line-height:23px;top:2185px}
.field{background:rgba(255,255,255,.22);color:#fff;font-size:12px;font-weight:700;padding:10px 14px}
.send-btn{left:554px;top:2496px;width:90px;height:38px;border:2px solid #fff;color:#fff;font-size:13px;font-weight:700;display:flex;align-items:center;justify-content:center}
.foot-nav{left:0;width:1200px;top:2586px;display:flex;justify-content:center;gap:22px;color:#fff;font-size:12px;font-weight:700}
.foot-nav i{font-style:normal;opacity:.8}
.foot-rule{left:98px;top:2628px;width:1004px;height:1px;background:rgba(255,255,255,.35)}
.copyright{left:98px;top:2647px;color:#fff;font-size:13px;font-weight:700}
.social{top:2641px;width:32px;height:32px;border:1.5px solid #fff;border-radius:50%}
</style>
</head>
<body>
<div class="page">

  <header class="site-header abs">
    <div class="brand abs"><div class="brand-mark"></div><div class="brand-name">SkyLoftReels</div></div>
    <div class="top-contact abs">
      <span><span class="ring"><svg width="14" height="14" viewBox="0 0 24 24"><path d="M6 3l4 4-2 3c1 2 3 4 6 6l3-2 4 4-3 3C10 20 4 14 3 6z" fill="none" stroke="#555" stroke-width="2"/></svg></span>+31647208351</span>
      <span><span class="ring"><svg width="14" height="12" viewBox="0 0 24 18"><rect x="1" y="1" width="22" height="16" fill="none" stroke="#555" stroke-width="2"/><path d="M1 1l11 9 11-9" fill="none" stroke="#555" stroke-width="2"/></svg></span>contact@skyloftreels.example</span>
    </div>
    <nav class="main-nav abs">
      <span class="active">HOME</span><span>ABOUT US</span><span>SERVICES</span><span>PRICES</span><span>PORTFOLIO</span><span>CONTAC US</span>
    </nav>
  </header>

  <section class="hero abs" role="img" aria-label="Photo of a white two-storey house with a drone in the sky and a realtor holding a controller"></section>
  <h1 class="hero-title abs">SkyLoftReels</h1>
  <p class="hero-sub abs">We Film Your Home To Increase Your Chances Of Sale</p>

  <section class="how abs"></section>
  <h2 class="section-title abs" style="top:697px">How Does <b>It Work?</b></h2>
  <div class="rule abs" style="top:754px"></div>
  <div class="video-slot abs" role="img" aria-label="Hands holding a tablet playing an aerial drone video of a house"></div>
  <div class="video-screen abs" role="img" aria-label="Aerial view of a house with a drone"></div>
  <div class="play abs" style="left:576px;top:914px"><svg width="26" height="28" viewBox="0 0 26 28"><path d="M2 1l23 13L2 27z" fill="var(--teal)"/></svg></div>

  <section class="help-bar abs">
    <div class="help-title abs">Need Help ?</div>
    <div class="help-icon abs" style="left:386px"><svg width="30" height="30" viewBox="0 0 32 32"><circle cx="16" cy="16" r="14" fill="none" stroke="#fff" stroke-width="1.5"/><path d="M11 9l3 3-1.5 2c1 1.5 2.5 3 4.5 4.5l2-1.5 3 3-2 2C14 21 10 17 9 11z" fill="none" stroke="#fff" stroke-width="1.5"/></svg></div>
    <div class="help-text abs" style="left:456px">+31647208351</div>
    <div class="help-icon abs" style="left:650px"><svg width="30" height="30" viewBox="0 0 32 32"><circle cx="16" cy="16" r="14" fill="none" stroke="#fff" stroke-width="1.5"/><rect x="9" y="11" width="14" height="10" fill="none" stroke="#fff" stroke-width="1.5"/><path d="M9 11l7 6 7-6" fill="none" stroke="#fff" stroke-width="1.5"/></svg></div>
    <div class="help-text abs" style="left:720px">contact@skyloftreels.example</div>
  </section>

  <section class="work abs" role="img" aria-label="Dim aerial photo of suburban houses and trees"></section>
  <h2 class="section-title on-dark abs" style="top:1255px">Our <b>Work</b></h2>
  <div class="rule on-dark abs" style="top:1312px"></div>
  <div class="arrow abs" style="left:48px"><svg width="10" height="12" viewBox="0 0 10 12"><path d="M9 1L2 6l7 5" fill="none" stroke="#fff" stroke-width="1.5"/></svg></div>
  <div class="arrow abs" style="left:1120px"><svg width="10" height="12" viewBox="0 0 10 12"><path d="M1 1l7 5-7 5" fill="none" stroke="#fff" stroke-width="1.5"/></svg></div>
  <div class="thumb abs" style="left:102px" role="img" aria-label="Drone flying over a brick house"><div class="play" style="width:44px;height:44px"><svg width="16" height="18" viewBox="0 0 26 28"><path d="M2 1l23 13L2 27z" fill="var(--teal)"/></svg></div></div>
  <div class="thumb abs" style="left:452px" role="img" aria-label="Drone above a two-storey brick house"><div class="play" style="width:44px;height:44px"><svg width="16" height="18" viewBox="0 0 26 28"><path d="M2 1l23 13L2 27z" fill="var(--teal)"/></svg></div></div>
  <div class="thumb abs" style="left:805px" role="img" aria-label="Hand launching a drone in front of a house"><div class="play" style="width:44px;height:44px"><svg width="16" height="18" viewBox="0 0 26 28"><path d="M2 1l23 13L2 27z" fill="var(--teal)"/></svg></div></div>

  <section class="why abs"></section>
  <h2 class="section-title abs" style="top:1591px">Why <b>Choose Us?</b></h2>
  <div class="rule abs" style="top:1648px"></div>

  <div class="feature left abs" style="left:104px;top:1684px"><h3>Cheap</h3><p>Lorem ipsum dolor sit amet, consectetuer adipiscing sed diam nonummy nibh euismod tincidunt umagna .gdag aliquam erat volutpat. tincidunt ut laoreetfgf</p><a>Read More &gt;&gt;</a></div>
  <div class="feature left abs" style="left:104px;top:1827px"><h3>4k Quality</h3><p>Lorem ipsum dolor sit amet, consectetuer adipiscing sed diam nonummy nibh euismod tincidunt umagna .gdag aliquam erat volutpat. tincidunt ut laoreetfgf</p><a>Read More &gt;&gt;</a></div>
  <div class="feature right abs" style="left:778px;top:1684px"><h3>Flexible</h3><p>Lorem ipsum dolor sit amet, consectetuer adipiscing sed diam nonummy nibh euismod tincidunt umagna gdag aliquam erat volutpat. tincidunt ut laoreetfgf.</p><a>Read More &gt;&gt;</a></div>
  <div class="feature right abs" style="left:778px;top:1827px"><h3>Increase Sale Chance</h3><p>Lorem ipsum dolor sit amet, consectetuer adipiscing sed diam nonummy nibh euismod tincidunt umagna gdag aliquam erat volutpat. tincidunt ut laoreetfgf.</p><a>Read More &gt;&gt;</a></div>

  <div class="icon-circle on abs" style="left:456px;top:1679px"><svg width="50" height="50" viewBox="0 0 50 50"><path d="M10 22L26 6h16v16L26 38z" fill="#fff" transform="rotate(10 25 25)"/><circle cx="36" cy="13" r="3" fill="var(--teal)"/><text x="20" y="30" font-size="12" font-weight="700" fill="var(--teal)" font-family="Raleway,sans-serif">%</text></svg></div>
  <div class="icon-circle abs" style="left:612px;top:1679px"><svg width="50" height="50" viewBox="0 0 50 50"><path d="M14 30a12 12 0 0 1 16-18" fill="none" stroke="#fff" stroke-width="6"/><path d="M36 20a12 12 0 0 1-16 18" fill="none" stroke="#fff" stroke-width="6"/><path d="M28 6l6 7-9 2z" fill="#fff"/><path d="M22 44l-6-7 9-2z" fill="#fff"/></svg></div>
  <div class="icon-circle abs" style="left:456px;top:1828px"><svg width="50" height="50" viewBox="0 0 50 50"><rect x="8" y="10" width="30" height="30" rx="4" fill="none" stroke="#fff" stroke-width="4"/><path d="M15 24l8 8 20-20" fill="none" stroke="#fff" stroke-width="6"/></svg></div>
  <div class="icon-circle abs" style="left:612px;top:1828px"><svg width="50" height="50" viewBox="0 0 50 50"><rect x="8" y="32" width="6" height="10" fill="#fff"/><rect x="17" y="26" width="6" height="16" fill="#fff"/><rect x="26" y="20" width="6" height="22" fill="#fff"/><rect x="35" y="14" width="6" height="28" fill="#fff"/><path d="M8 26l12-10 8 5 14-13" fill="none" stroke="#fff" stroke-width="3"/></svg></div>

  <section class="contact abs" role="img" aria-label="Aerial photo of a large house among trees, darkened"></section>
  <h2 class="section-title on-dark abs" style="top:2022px">Contact <b>Us</b></h2>
  <div class="contact-panel abs"></div>
  <div class="send-icon abs"><svg width="26" height="26" viewBox="0 0 26 26"><path d="M2 12L24 2 16 24l-4-9z" fill="none" stroke="#333" stroke-width="1.8"/><path d="M12 15L24 2" stroke="#333" stroke-width="1.8"/></svg></div>
  <div class="contact-info abs">Lorem ipsum dolor sit amet, consectetuer adipiscing elit, sed diam nonummy<br>contact@skyloftreels.example<br>+31647208351</div>
  <div class="field abs" style="left:254px;top:2283px;width:341px;height:38px">Name</div>
  <div class="field abs" style="left:603px;top:2283px;width:343px;height:38px">Phone</div>
  <div class="field abs" style="left:254px;top:2330px;width:692px;height:37px">Email</div>
  <div class="field abs" style="left:254px;top:2376px;width:692px;height:100px">Message</div>
  <div class="send-btn abs">SEND</div>

  <nav class="foot-nav abs"><span>HOME</span><i>|</i><span>ABOUT US</span><i>|</i><span>SERVICES</span><i>|</i><span>PRICES</span><i>|</i><span>PORTFOLIO</span><i>|</i><span>CONTAC US</span></nav>
  <div class="foot-rule abs"></div>
  <p class="copyright abs">Copyright © 2016 SkyLoftReels. I All Rights Reserved</p>
  <div class="social abs" style="left:1024px"></div>
  <div class="social abs" style="left:1069px"></div>

</div>
</body>
</html>
```